Corvel Capital LLC

Need Professional Business cards for New Investment Fund

Target Market(s)

High Quality investors

Industry/Entity Type

Financial

Contact Information for Business Card

Phone Number +1 555 284 6190
Name Lukas Varenko
Title Fund Manager
email lv@FundCorvel.com
Website www.FundCorvel.com

Colors

Designer to choose colors to be used in the design.

Requirements
Must have
• Must have our Logo and all of the above. Must be made so lettering and loge can be raised

```html
<!DOCTYPE html>
<html lang="en">
<head>
<meta charset="utf-8">
<title>Halvyn – Business Card</title>
<link rel="stylesheet" href="https://fonts.googleapis.com/css2?family=Questrial&display=swap">
<style>
  :root {
    --stage: #e6e7e6;
    --card-dark: #434f43;
    --card-light: #ffffff;
    --accent: #22e30a;
    --ink: #3f3f3f;
    --paper-text: #ffffff;
  }
  * { margin: 0; padding: 0; box-sizing: border-box; }
  html, body {
    width: 1200px; height: 960px; overflow: hidden;
    background: var(--stage);
    font-family: "Questrial", "Century Gothic", sans-serif;
  }
  .stage { position: relative; width: 1200px; height: 960px; }
  .card {
    position: absolute; left: 280px; width: 640px; height: 366px;
    box-shadow: 0 10px 28px rgba(0,0,0,0.18);
  }
  .card--back { top: 92px; background: var(--card-dark); }
  .card--front { top: 502px; background: var(--card-light); }

  /* back side */
  .back-brand {
    position: absolute; left: 0; right: 0; top: 136px;
    display: flex; justify-content: center; align-items: center; gap: 14px;
  }
  .brand-mark { width: 22px; height: 22px; background: var(--paper-text); flex: none; }
  .back-brand .brand-name {
    color: var(--paper-text); font-size: 40px; line-height: 48px; letter-spacing: 3px;
  }
  .back-web {
    position: absolute; left: 0; right: 0; top: 212px; text-align: center;
    color: var(--paper-text); font-size: 17px; letter-spacing: 2px;
  }

  /* front side */
  .front-brand {
    position: absolute; left: 56px; top: 148px;
    display: flex; align-items: center; gap: 12px;
  }
  .front-brand .brand-mark { background: var(--accent); width: 26px; height: 26px; }
  .front-brand .brand-name { color: var(--accent); font-size: 48px; line-height: 56px; }
  .holder { position: absolute; left: 370px; top: 110px; }
  .holder-name { color: var(--accent); font-size: 27px; font-weight: 400; line-height: 32px; }
  .holder-title { color: var(--ink); font-size: 17px; line-height: 22px; margin-top: 2px; }
  .contacts { list-style: none; margin-top: 20px; }
  .contacts li {
    display: flex; align-items: center; gap: 12px;
    color: var(--ink); font-size: 18px; line-height: 24px; white-space: nowrap;
  }
  .contacts svg { width: 14px; height: 14px; fill: var(--accent); flex: none; }
</style>
</head>
<body>
<main class="stage">
  <section class="card card--back" aria-label="Card back">
    <div class="back-brand">
      <span class="brand-mark"></span>
      <span class="brand-name">HALVYN</span>
    </div>
    <p class="back-web">www.FundCorvel.com</p>
  </section>

  <section class="card card--front" aria-label="Card front">
    <div class="front-brand">
      <span class="brand-mark"></span>
      <span class="brand-name">Halvyn</span>
    </div>
    <div class="holder">
      <h1 class="holder-name">Lukas Varenko</h1>
      <p class="holder-title">Fund Manager</p>
      <ul class="contacts">
        <li>
          <svg viewBox="0 0 16 16" aria-hidden="true"><path d="M3.5 1l3 3-1.6 1.8c.9 1.9 2.4 3.4 4.3 4.3L11 8.5l3 3-2 2.5C6.5 13.5 2.5 9.5 1 4z"/></svg>
          +1 555 284 6190
        </li>
        <li>
          <svg viewBox="0 0 16 16" aria-hidden="true"><path d="M1 3h14v10H1z"/><path d="M2 4.5l6 4.5 6-4.5" fill="none" stroke="#fff" stroke-width="1.2"/></svg>
          lv@FundCorvel.com
        </li>
        <li>
          <svg viewBox="0 0 16 16" aria-hidden="true"><circle cx="8" cy="8" r="7"/><path d="M1 8h14M8 1c-3 3.5-3 10.5 0 14M8 1c3 3.5 3 10.5 0 14" fill="none" stroke="#fff" stroke-width="1"/></svg>
          www.FundCorvel.com
        </li>
      </ul>
    </div>
  </section>
</main>
</body>
</html>
```